eBook-Cover für Thriller gesucht
An dieser Stelle ein großes Lob und vielen Dank an die Designerin Larosa. Auch das zweite Buchcover ist wieder überaus gelungen, eine ganz tolle Arbeit. Auch die angenehme Zusammenarbeit war mir, wie schon beim ersten Auftrag, eine Freude. Ebenso hervorzuheben ist die Schnelligkeit und Kreativität, mit der die Designerin auf Änderungswünsche reagiert. Als Auftraggeber gebe ich verdiente fünf Sterne und bin mit dem Ergebnis wirklich sehr zufrieden.
Zielgruppe
Ich bin Autor. Zielgruppe sind (anspruchsvolle) Leser/innen von Thrillern und Kriminalromanen im ebook-Bereich.
Aufgabenstellung
- Gesucht wird ein ebook-Cover für einen Thriller mit dem Titel 'Kaltgrund'
- Grobe Aufteilung siehe Skizzen
- Fokus des Covers liegt auf dem Buchtitel und dem Motiv ('Blauer Drachen')
- Hintergrund eher hell, Assoziation mit zarter Eisfläche mit angedeuteten Rissen vom Hauptmotiv ausgehend. Dadurch auch Tiefe und Dreidimensionalität. (Beispiel zum Hintergrund: 'Schattenfrist' von Heinrich Wendel, jedoch ohne Blut )
-Titelschrift groß, Stil 'gekratzt' bzw. 'gestrichelt', (Schriftart ähnlich wie Autorenname bei 'Die Schleuse' von Matthias Kolbe). Schrift groß und 'treppenförmig' neben dem Hauptmotiv angeordnet. Schriftfarbe schwarz/dunkelblau, ähnlich Hauptmotiv (Bsp.: 'Schwarzeid' von Heinrich Wendel)
Hauptmotiv ist der vom rechten Coverrand hineinragende 'Blaue Drachen' (Glaucus atlanticus, siehe hochgeladenes Beispielbild von Wissnetz)
- Schriftart von Autorenname und Genre eher klar
- eigene Detailvorschläge zur Optimierung des Ergebnisses möglich bzw. erwünscht

```html
<!DOCTYPE html>
<html lang="de">
<head>
<meta charset="utf-8">
<title>Kaltgrund – Konrad Velten</title>
<link href="https://fonts.googleapis.com/css2?family=Barlow:wght@400&family=Rubik+Dirt&display=swap" rel="stylesheet">
<style>
  :root {
    --ice-light: #eef6fa;
    --ice-mid: #bcdcea;
    --ice-deep: #7fb2cf;
    --crack: #5f93b4;
    --author-blue: #2f5f93;
    --title-navy: #0e2a57;
    --dragon-blue: #2c4fa8;
    --dragon-dark: #1b2553;
  }
  html, body {
    margin: 0;
    padding: 0;
    width: 750px;
    height: 1200px;
    overflow: hidden;
  }
  .cover {
    position: relative;
    width: 750px;
    height: 1200px;
    overflow: hidden;
    background:
      radial-gradient(ellipse at 20% 30%, var(--ice-light) 0%, transparent 55%),
      radial-gradient(ellipse at 70% 80%, #f4fafd 0%, transparent 50%),
      radial-gradient(ellipse at 0% 100%, var(--ice-deep) 0%, transparent 45%),
      radial-gradient(ellipse at 100% 0%, var(--ice-deep) 0%, transparent 40%),
      linear-gradient(160deg, var(--ice-mid), #d9ecf4 50%, var(--ice-mid));
  }
  .cracks {
    position: absolute;
    inset: 0;
  }
  .author {
    position: absolute;
    top: 68px;
    left: 0;
    width: 100%;
    margin: 0;
    text-align: center;
    font-family: "Barlow", sans-serif;
    font-weight: 400;
    font-size: 90px;
    letter-spacing: 1px;
    color: var(--author-blue);
    line-height: 1;
  }
  .dragon {
    position: absolute;
    left: 300px;
    top: 250px;
    width: 410px;
    height: 480px;
    border-radius: 50%;
    background: radial-gradient(ellipse at 55% 45%, var(--dragon-dark) 0%, var(--dragon-blue) 28%, rgba(44,79,168,0.3) 52%, transparent 70%);
  }
  .title {
    position: absolute;
    inset: 0;
    margin: 0;
  }
  .title svg {
    display: block;
  }
  .title-line {
    font-family: "Rubik Dirt", sans-serif;
    font-weight: 400;
    font-size: 208px;
    fill: var(--title-navy);
  }
  .genre {
    position: absolute;
    top: 1066px;
    left: 0;
    width: 100%;
    margin: 0;
    text-align: center;
    font-family: "Barlow", sans-serif;
    font-weight: 400;
    font-size: 42px;
    letter-spacing: 2px;
    color: var(--author-blue);
    padding-left: 10px;
    line-height: 1;
  }
</style>
</head>
<body>
  <main class="cover">
    <svg class="cracks" width="750" height="1200" viewBox="0 0 750 1200" aria-hidden="true">
      <g fill="none" stroke="var(--crack)" stroke-width="2" stroke-linecap="round" opacity="0.55">
        <path d="M470 400 L490 300 L500 200 L540 120 L560 40"/>
        <path d="M420 480 L330 440 L250 420 L150 330 L60 300"/>
        <path d="M400 560 L340 620 L300 700 L200 760 L240 820"/>
        <path d="M200 760 L230 880 L250 960 L130 1000 L60 1060 L50 1150"/>
        <path d="M540 550 L640 600 L740 620"/>
        <path d="M560 620 L500 560"/>
        <path d="M130 1000 L20 990"/>
      </g>
    </svg>

    <h2 class="author">KONRAD VELTEN</h2>

    <div class="dragon" role="img" aria-label="Blauer Drachen (Glaucus atlanticus), der vom rechten Rand ins Eis ragt"></div>

    <h1 class="title" aria-label="Kaltgrund">
      <svg width="750" height="1200" viewBox="0 0 750 1200" aria-hidden="true">
        <defs>
          <filter id="title-shadow" x="-5%" y="-5%" width="110%" height="115%">
            <feDropShadow dx="2" dy="3" stdDeviation="2" flood-color="#0e2a57" flood-opacity="0.25"/>
          </filter>
        </defs>
        <g filter="url(#title-shadow)">
          <text class="title-line" x="15" y="486" textLength="327" lengthAdjust="spacingAndGlyphs">KAL</text>
          <text class="title-line" x="122" y="759" textLength="298" lengthAdjust="spacingAndGlyphs">TGR</text>
          <text class="title-line" x="426" y="888" textLength="240" lengthAdjust="spacingAndGlyphs">UND</text>
        </g>
      </svg>
    </h1>

    <p class="genre">THRILLER</p>
  </main>
</body>
</html>
```